New florist business website design

Number 1 want is an easy to navigate & check out website
Needs to be beautiful and eye catching as well.
This is an online only business (no shop front)
Rustic and blush pinks, neutrals, woods, leaves
Customers need to be able to go onto my website, select something they want to buy but have the option to use a drop down box to change colours of the flowers, or add notes to make changes to the arrangement

Industry/Entity Type

Florist

Coding

Coded - Design and coding required

Number of Pages Required

5+ page

Colors
f9d9e8
fff2ec
fffefc

Requirements
Must have
• Drop down menu to take you to other pages for Arrangements, bouquets, everlasting arrangements, gifts, contact
Be able to purchase and “add to basket”
Checkout page
Nice to have
• Be able to add my own photos once I’ve taken new ones
Should not have
• Tacky images or clip art

```html
<!DOCTYPE html>
<html lang="en">
<head>
<meta charset="utf-8">
<title>Petal &amp; Fern — Florist</title>
<link rel="stylesheet" href="https://fonts.googleapis.com/css2?family=Roboto:wght@400;500;700&family=Alex+Brush&display=swap">
<style>
:root{
  --blush:#f9d9e8;
  --blush-deep:#f7b8d3;
  --peach:#fff2ec;
  --cream:#fffefc;
  --ink:#1d1d1d;
  --muted:#6f6f6f;
  --ring:#fbd9b8;
  --card-bg:#f5f5f5;
  --line:#e6e6e6;
}
*{box-sizing:border-box;margin:0;padding:0}
html,body{width:1200px;height:3609px;overflow:hidden}
body{position:relative;background:var(--cream);font-family:"Roboto",sans-serif;color:var(--ink)}
.abs{position:absolute}
.script{font-family:"Alex Brush",cursive;font-weight:400;color:var(--ink)}

/* header */
.site-header{left:0;top:0;width:1200px;height:147px;background:var(--cream);border-bottom:1px solid #eee}
.brand{left:112px;top:48px;font-size:26px;font-weight:400;letter-spacing:.5px;color:#3a3a3a;display:flex;align-items:center;gap:10px}
.brand-dot{width:14px;height:14px;border-radius:50%;background:var(--blush-deep)}
.search{left:518px;top:25px;width:337px;height:45px;border:1px solid #e4e4e4;background:#fff;display:flex;align-items:center}
.search span{flex:1;padding-left:20px;font-size:13px;color:#777}
.search-btn{width:44px;height:39px;margin-right:2px;background:var(--blush);display:flex;align-items:center;justify-content:center}
.account{left:900px;top:38px;font-size:13px;font-weight:500;color:#444;display:flex;align-items:center;gap:10px}
.cart{left:1046px;top:32px;width:34px;height:34px;border:2px solid var(--blush);border-radius:50%;display:flex;align-items:center;justify-content:center}
.cart-count{left:1072px;top:30px;font-size:10px;font-weight:700}
.main-nav{left:355px;top:99px;display:flex;gap:0;font-size:13px;font-weight:700}
.main-nav a{color:var(--ink);text-decoration:none;margin-right:28px;display:flex;align-items:center;gap:6px}
.caret{width:0;height:0;border-left:4px solid transparent;border-right:4px solid transparent;border-top:5px solid var(--ink)}

/* hero */
.hero{left:0;top:147px;width:1200px;height:631px;background:linear-gradient(90deg,#d9d9d9 0%,#ececec 45%,#f4f4f4 55%)}
.hero-photo{left:560px;top:147px;width:640px;height:631px;background:radial-gradient(circle at 55% 45%,#f39b82 0%,#f4b3a0 35%,#e7c4b8 60%,#ececec 100%)}
.hero-title{left:110px;top:268px;font-size:58px}
.hero-text{left:111px;top:357px;width:430px;font-size:13.5px;line-height:25px;color:#555}
.btn{display:flex;align-items:center;gap:10px;background:var(--blush);font-size:13.5px;font-weight:700;color:var(--ink);padding:0 16px;height:45px}

/* occasions */
.occasions{left:0;top:805px;width:1200px;height:820px;background:radial-gradient(ellipse at 50% 40%,var(--peach) 0%,#fdf0ea 55%,var(--cream) 100%)}
.section-title{left:0;width:1200px;text-align:center;font-size:44px}
.occasion{width:240px;text-align:center}
.occasion-ring{width:228px;height:228px;margin:0 auto;border-radius:50%;background:var(--ring);display:flex;align-items:center;justify-content:center}
.occasion-photo{width:200px;height:200px;border-radius:50%}
.occasion-label{margin-top:26px;font-size:34px;white-space:nowrap}

/* products */
.product{width:237px;height:306px;background:#fff;box-shadow:0 2px 8px rgba(0,0,0,.08)}
.product-photo{height:220px;background:var(--card-bg);display:flex;align-items:center;justify-content:center}
.product-photo div{width:170px;height:180px;border-radius:50% 50% 40% 40%}
.product-info{display:flex;justify-content:space-between;align-items:center;padding:0 17px;height:50px;border-bottom:1px solid var(--line)}
.product-title{font-size:13px;font-weight:700}
.product-price{font-size:12px;color:#777;font-weight:500}
.product-meta{display:flex;justify-content:space-between;align-items:center;padding:0 17px;height:36px;font-size:9.5px;font-weight:500;color:#555}
.product-meta .truck{display:flex;align-items:center;gap:10px}
.wish{width:22px;height:22px;border:1px solid #555;border-radius:50%}
.arrow{width:40px;height:40px;border-radius:50%;background:#fff;box-shadow:0 1px 6px rgba(0,0,0,.15);display:flex;align-items:center;justify-content:center}

/* deal */
.deal{left:0;top:2182px;width:1200px;height:355px;background:linear-gradient(90deg,#eeeeee,#f7f7f7)}
.deal-photo{left:0;top:2182px;width:470px;height:355px;background:radial-gradient(circle at 45% 50%,#f08cb0 0%,#f6c9a0 35%,#e9e9e9 75%)}
.deal-title{left:557px;top:2238px;font-size:86px}
.deal-text{left:557px;top:2364px;font-size:14px;color:#555}

/* footer */
.footer-col h4{font-size:13px;font-weight:700;text-decoration:underline;margin-bottom:14px}
.footer-col li{list-style:none;font-size:13.5px;color:#555;height:37px;display:flex;align-items:center;gap:14px}
.chev{font-size:12px;color:#555}
.socials{display:flex;gap:10px}
.social{width:31px;height:31px;border:2px solid var(--ink);border-radius:50%}
.newsletter{left:779px;top:3442px;width:312px;height:48px;background:#fff;border:1px solid #e2e2e2;display:flex;align-items:center}
.newsletter span{flex:1;padding-left:17px;font-size:13.5px;color:#666}
.newsletter-btn{width:44px;height:42px;margin-right:2px;background:var(--blush);display:flex;align-items:center;justify-content:center}
.copyright{left:0;top:3555px;width:1200px;height:54px;background:var(--blush-deep);display:flex;align-items:center;justify-content:center;font-size:13px;color:#fff}
</style>
</head>
<body>

<header class="abs site-header">
  <div class="abs brand"><span class="brand-dot"></span>Petal &amp; Fern</div>
  <div class="abs search"><span>Search Products</span><div class="search-btn">
    <svg width="14" height="14" viewBox="0 0 14 14"><circle cx="6" cy="6" r="4.5" fill="none" stroke="#222" stroke-width="2"/><line x1="9.3" y1="9.3" x2="13" y2="13" stroke="#222" stroke-width="2"/></svg></div></div>
  <div class="abs account"><svg width="12" height="12" viewBox="0 0 12 12"><circle cx="6" cy="3.5" r="3" fill="var(--blush-deep)"/><path d="M0 12c0-4 12-4 12 0z" fill="var(--blush-deep)"/></svg>MY ACCOUNT</div>
  <div class="abs cart"><svg width="16" height="14" viewBox="0 0 16 14"><path d="M1 1h3l2 8h8l2-6H5" fill="none" stroke="var(--blush-deep)" stroke-width="1.6"/><circle cx="7" cy="12" r="1.3" fill="var(--blush-deep)"/><circle cx="13" cy="12" r="1.3" fill="var(--blush-deep)"/></svg></div>
  <div class="abs cart-count">0</div>
  <nav class="abs main-nav">
    <a>HOME</a>
    <a>ARRANGEMENTS <span class="caret"></span></a>
    <a>BOUQUETS <span class="caret"></span></a>
    <a>EVERLASTING ARRANGEMENTS <span class="caret"></span></a>
    <a>GIFTS <span class="caret"></span></a>
    <a>CONTACT</a>
  </nav>
</header>

<section>
  <div class="abs hero"></div>
  <div class="abs hero-photo" role="img" aria-label="Bouquet of peach and pink roses with succulents"></div>
  <h1 class="abs script hero-title">Celebrate Spring</h1>
  <p class="abs hero-text">Lorem ipsum dolor sit amet, consectetur adipiscing elit, sed do eiusmod tempor incididunt ut labore et dolor</p>
  <div class="abs btn" style="left:111px;top:434px">SHOP FLOWERS <svg width="12" height="11" viewBox="0 0 12 11"><path d="M0 1h2.5l1.5 6h6.5l1.5-5H3.5z" fill="#222"/><circle cx="5" cy="9.5" r="1.2" fill="#222"/><circle cx="10" cy="9.5" r="1.2" fill="#222"/></svg></div>
</section>

<section>
  <div class="abs occasions"></div>
  <h2 class="abs script section-title" style="top:852px">Shop by Popular Occasions</h2>
  <div class="abs occasion" style="left:163px;top:961px"><div class="occasion-ring"><div class="occasion-photo" role="img" aria-label="Wedding bouquet of coral and cream roses" style="background:radial-gradient(#f2a189,#e9c9bd)"></div></div><div class="script occasion-label">Wedding</div></div>
  <div class="abs occasion" style="left:491px;top:961px"><div class="occasion-ring"><div class="occasion-photo" role="img" aria-label="Couple holding a bouquet" style="background:radial-gradient(#d9b9a8,#a58d84)"></div></div><div class="script occasion-label">Love &amp; Romance</div></div>
  <div class="abs occasion" style="left:820px;top:961px"><div class="occasion-ring"><div class="occasion-photo" role="img" aria-label="Get well bouquet in a vase" style="background:radial-gradient(#f1c36a,#dfe3e6)"></div></div><div class="script occasion-label">Get Well</div></div>
  <div class="abs occasion" style="left:320px;top:1294px"><div class="occasion-ring"><div class="occasion-photo" role="img" aria-label="White lilies and roses sympathy arrangement" style="background:radial-gradient(#eef0e6,#9aa79a)"></div></div><div class="script occasion-label">Sympathy &amp; Funeral</div></div>
  <div class="abs occasion" style="left:645px;top:1294px"><div class="occasion-ring"><div class="occasion-photo" role="img" aria-label="Family with a bouquet for Father's Day" style="background:radial-gradient(#f0d27a,#8fc0c9)"></div></div><div class="script occasion-label">Father's Day</div></div>
</section>

<section>
  <h2 class="abs script section-title" style="top:1677px">Our Best Selling Flowers &amp; Gifts</h2>
  <div class="abs arrow" style="left:25px;top:1916px"><svg width="10" height="16" viewBox="0 0 10 16"><path d="M8 2 2 8l6 6" fill="none" stroke="#222" stroke-width="2"/></svg></div>
  <div class="abs arrow" style="left:1134px;top:1916px"><svg width="10" height="16" viewBox="0 0 10 16"><path d="M2 2l6 6-6 6" fill="none" stroke="#222" stroke-width="2"/></svg></div>

  <article class="abs product" style="left:102px;top:1782px"><div class="product-photo"><div role="img" aria-label="White and green bouquet" style="background:radial-gradient(#f3f3ec,#9fb08a)"></div></div><div class="product-info"><span class="product-title">PRODUCT TITLE</span><span class="product-price">$50.00</span></div><div class="product-meta"><span class="truck"><svg width="12" height="9" viewBox="0 0 12 9"><rect x="0" y="1" width="7" height="6" fill="#444"/><path d="M7 3h3l2 2v2H7z" fill="#444"/></svg>SAME DAY DELIVERY</span><span class="wish"></span></div></article>
  <article class="abs product" style="left:355px;top:1782px"><div class="product-photo"><div role="img" aria-label="Red rose bouquet" style="background:radial-gradient(#d81d2a,#6f8a4a)"></div></div><div class="product-info"><span class="product-title">PRODUCT TITLE</span><span class="product-price">$50.00</span></div><div class="product-meta"><span class="truck"><svg width="12" height="9" viewBox="0 0 12 9"><rect x="0" y="1" width="7" height="6" fill="#444"/><path d="M7 3h3l2 2v2H7z" fill="#444"/></svg>SAME DAY DELIVERY</span><span class="wish"></span></div></article>
  <article class="abs product" style="left:609px;top:1782px"><div class="product-photo"><div role="img" aria-label="Purple and pink mixed bouquet" style="background:radial-gradient(#b23a86,#6e7a52)"></div></div><div class="product-info"><span class="product-title">PRODUCT TITLE</span><span class="product-price">$50.00</span></div><div class="product-meta"><span class="truck"><svg width="12" height="9" viewBox="0 0 12 9"><rect x="0" y="1" width="7" height="6" fill="#444"/><path d="M7 3h3l2 2v2H7z" fill="#444"/></svg>SAME DAY DELIVERY</span><span class="wish"></span></div></article>
  <article class="abs product" style="left:862px;top:1782px"><div class="product-photo"><div role="img" aria-label="Mixed tulip bouquet" style="background:radial-gradient(#f0d6e6,#7aa65c)"></div></div><div class="product-info"><span class="product-title">PRODUCT TITLE</span><span class="product-price">$50.00</span></div><div class="product-meta"><span class="truck"><svg width="12" height="9" viewBox="0 0 12 9"><rect x="0" y="1" width="7" height="6" fill="#444"/><path d="M7 3h3l2 2v2H7z" fill="#444"/></svg>SAME DAY DELIVERY</span><span class="wish"></span></div></article>
</section>

<section>
  <div class="abs deal"></div>
  <div class="abs deal-photo" role="img" aria-label="Pink dahlias, roses and fuchsias on a white table"></div>
  <h2 class="abs script deal-title">Deal Of the Day</h2>
  <p class="abs deal-text">Sed ut perspiciatis unde omnis iste natus error sit voluptatem accusantium</p>
  <div class="abs btn" style="left:557px;top:2414px">SHOP FLOWERS <svg width="12" height="11" viewBox="0 0 12 11"><path d="M0 1h2.5l1.5 6h6.5l1.5-5H3.5z" fill="#222"/><circle cx="5" cy="9.5" r="1.2" fill="#222"/><circle cx="10" cy="9.5" r="1.2" fill="#222"/></svg></div>
</section>

<section>
  <h2 class="abs script section-title" style="top:2620px">Shop Best Sellers</h2>
  <div class="abs arrow" style="left:25px;top:2859px"><svg width="10" height="16" viewBox="0 0 10 16"><path d="M8 2 2 8l6 6" fill="none" stroke="#222" stroke-width="2"/></svg></div>
  <div class="abs arrow" style="left:1134px;top:2859px"><svg width="10" height="16" viewBox="0 0 10 16"><path d="M2 2l6 6-6 6" fill="none" stroke="#222" stroke-width="2"/></svg></div>

  <article class="abs product" style="left:102px;top:2725px"><div class="product-photo"><div role="img" aria-label="Bright mixed bouquet" style="background:radial-gradient(#e8742c,#b1318a)"></div></div><div class="product-info"><span class="product-title">PRODUCT TITLE</span><span class="product-price">$50.00</span></div><div class="product-meta"><span class="truck"><svg width="12" height="9" viewBox="0 0 12 9"><rect x="0" y="1" width="7" height="6" fill="#444"/><path d="M7 3h3l2 2v2H7z" fill="#444"/></svg>SAME DAY DELIVERY</span><span class="wish"></span></div></article>
  <article class="abs product" style="left:355px;top:2725px"><div class="product-photo"><div role="img" aria-label="White and blush rose bouquet" style="background:radial-gradient(#f7e8df,#a5ab94)"></div></div><div class="product-info"><span class="product-title">PRODUCT TITLE</span><span class="product-price">$50.00</span></div><div class="product-meta"><span class="truck"><svg width="12" height="9" viewBox="0 0 12 9"><rect x="0" y="1" width="7" height="6" fill="#444"/><path d="M7 3h3l2 2v2H7z" fill="#444"/></svg>SAME DAY DELIVERY</span><span class="wish"></span></div></article>
  <article class="abs product" style="left:609px;top:2725px"><div class="product-photo"><div role="img" aria-label="Pink gerbera and rose bouquet" style="background:radial-gradient(#e86e8e,#3f7a3a)"></div></div><div class="product-info"><span class="product-title">PRODUCT TITLE</span><span class="product-price">$50.00</span></div><div class="product-meta"><span class="truck"><svg width="12" height="9" viewBox="0 0 12 9"><rect x="0" y="1" width="7" height="6" fill="#444"/><path d="M7 3h3l2 2v2H7z" fill="#444"/></svg>SAME DAY DELIVERY</span><span class="wish"></span></div></article>
  <article class="abs product" style="left:862px;top:2725px"><div class="product-photo"><div role="img" aria-label="Orange and yellow rose bouquet" style="background:radial-gradient(#f2a23a,#7e8a48)"></div></div><div class="product-info"><span class="product-title">PRODUCT TITLE</span><span class="product-price">$50.00</span></div><div class="product-meta"><span class="truck"><svg width="12" height="9" viewBox="0 0 12 9"><rect x="0" y="1" width="7" height="6" fill="#444"/><path d="M7 3h3l2 2v2H7z" fill="#444"/></svg>SAME DAY DELIVERY</span><span class="wish"></span></div></article>
</section>

<footer>
  <div class="abs footer-col" style="left:110px;top:3296px"><h4>QUICK LINKS</h4><ul>
    <li><span class="chev">»</span>Home</li><li><span class="chev">»</span>About Us</li><li><span class="chev">»</span>Our Products</li><li><span class="chev">»</span>Bouquets</li><li><span class="chev">»</span>Latest Blog</li></ul></div>
  <div class="abs footer-col" style="left:295px;top:3296px"><h4>OTHER LINKS</h4><ul>
    <li><span class="chev">»</span>Terms &amp; Conditions</li><li><span class="chev">»</span>Privacy Policy</li><li><span class="chev">»</span>Help Service</li><li><span class="chev">»</span>FAQ</li><li><span class="chev">»</span>Contact us</li></ul></div>
  <div class="abs footer-col" style="left:526px;top:3296px"><h4>FIND US ON</h4><ul>
    <li><svg width="10" height="13" viewBox="0 0 10 13"><path d="M5 0a5 5 0 0 1 5 5c0 3-5 8-5 8S0 8 0 5a5 5 0 0 1 5-5z" fill="#555"/><circle cx="5" cy="5" r="1.8" fill="#fff"/></svg>&nbsp;14 Meadow Lane,</li>
    <li style="padding-left:31px">Willow Creek</li>
    <li><svg width="12" height="12" viewBox="0 0 12 12"><path d="M2 0l3 3-1.5 2a7 7 0 0 0 3.5 3.5L9 7l3 3-2 2C5 12 0 7 0 2z" fill="#555"/></svg>&nbsp;1 555 010 200</li>
    <li><svg width="13" height="10" viewBox="0 0 13 10"><rect x=".6" y=".6" width="11.8" height="8.8" fill="none" stroke="#555" stroke-width="1.2"/><path d="M.6.6 6.5 5.5 12.4.6" fill="none" stroke="#555" stroke-width="1.2"/></svg>&nbsp;hello@petalandfern.com</li></ul></div>
  <div class="abs footer-col" style="left:779px;top:3295px"><h4>CONNECTED US ON</h4>
    <div class="socials"><span class="social"></span><span class="social"></span><span class="social"></span><span class="social"></span><span class="social"></span></div></div>
  <div class="abs footer-col" style="left:779px;top:3398px"><h4>SUBSCRIBE TO OUR NEWSLETTER</h4></div>
  <div class="abs newsletter"><span>Email Address</span><div class="newsletter-btn"><svg width="16" height="16" viewBox="0 0 16 16"><path d="M15 1 1 7l6 2 2 6z" fill="#222"/></svg></div></div>
  <div class="abs copyright">© 2021 Petal &amp; Fern. All Rights Reserved</div>
</footer>

</body>
</html>
```